Looking for a cool & simple business-card-design for digital agency

Hi!

We are a web agency that offers Reputation Management, Vextor & Seo Services and software development. We like cool things, we like innovative styles.

We have uploaded our logo.

Project Deadline Extended Reason: Client does not want any designs with the colorful logo. Please send us submissions ONLY with the blac and white logo. What the client would like to see:1) Back of the card: is a silver logo on a black background2) front of the card with all the data, please use white background and black logo thank you Added Friday, May 8, 2015

Industry/Entity Type

Software

```html
<!DOCTYPE html>
<html lang="de">
<head>
<meta charset="utf-8">
<title>Nordkante AG – Geschäftsausstattung</title>
<link href="https://fonts.googleapis.com/css2?family=Questrial&family=Great+Vibes&display=swap" rel="stylesheet">
<style>
  :root {
    --backdrop: #d9d9db;
    --paper: #fbfbfb;
    --ink: #1e1e1e;
    --muted: #555555;
    --rule: #c8c8c8;
    --folder: #2b2b2b;
    --folder-edge: #3a3a3a;
    --silver: #e6e6e6;
  }
  * { margin: 0; padding: 0; box-sizing: border-box; }
  html, body { width: 1200px; height: 1118px; overflow: hidden; }
  body {
    background: var(--backdrop);
    font-family: "Questrial", "Century Gothic", sans-serif;
    color: var(--ink);
    position: relative;
  }
  .piece { position: absolute; background: var(--paper); }

  .brand { position: absolute; display: flex; flex-direction: column; align-items: flex-start; }
  .brand-name { display: flex; align-items: center; gap: 4px; font-weight: 400; line-height: 1; }
  .brand-name .dot { display: inline-block; background: currentColor; }
  .brand-tag { letter-spacing: 0.28em; line-height: 1; margin-top: 2px; }

  /* Letterhead */
  .letterhead { left: 188px; top: 63px; width: 380px; height: 538px; }
  .letterhead .brand { left: 114px; top: 32px; }
  .letterhead .brand-name { font-size: 15px; }
  .letterhead .brand-name .dot { width: 9px; height: 9px; }
  .letterhead .brand-tag { font-size: 6.5px; }
  .letter-body { position: absolute; left: 36px; top: 175px; width: 284px; font-size: 5.4px; line-height: 7.2px; color: #333; }
  .letter-body p { margin-bottom: 5px; text-align: justify; }
  .letter-body .greeting { font-weight: 700; margin-bottom: 6px; }
  .closing { position: absolute; left: 36px; top: 343px; font-size: 5.4px; line-height: 7px; color: #333; }
  .closing strong { display: block; }
  .signature { position: absolute; left: 84px; top: 335px; width: 78px; height: 30px; background: linear-gradient(90deg, #e8ecf6, #dfe4f2); }
  .footer-rule { position: absolute; left: 86px; right: 86px; top: 508px; border-top: 1px solid var(--rule); }
  .letter-footer { position: absolute; left: 0; right: 0; top: 513px; text-align: center; font-size: 5.2px; line-height: 7px; color: #333; }

  /* Folder */
  .folder { left: 617px; top: 47px; width: 415px; height: 554px; background: var(--folder); border-radius: 6px 8px 8px 6px; }
  .folder .spine { position: absolute; left: 22px; top: 0; bottom: 0; width: 2px; background: var(--folder-edge); }
  .folder .brand { left: 118px; top: 80px; color: var(--silver); }
  .folder .brand-name { font-size: 21px; }
  .folder .brand-name .dot { width: 12px; height: 12px; }
  .folder .brand-tag { font-size: 9px; margin-top: 3px; }

  /* Envelopes */
  .envelope-front { left: 170px; top: 646px; width: 399px; height: 200px; }
  .envelope-front .brand { left: 24px; top: 22px; }
  .envelope-front .brand-name { font-size: 13px; }
  .envelope-front .brand-name .dot { width: 8px; height: 8px; }
  .envelope-front .brand-tag { font-size: 6px; }
  .envelope-front .return { position: absolute; left: 32px; top: 176px; font-size: 5.2px; line-height: 6.5px; color: #333; }
  .envelope-back { left: 616px; top: 646px; width: 401px; height: 200px; }
  .envelope-back .flap { position: absolute; left: 14px; right: 14px; top: 46px; border-top: 1px solid #e2e2e2; }
  .envelope-back .brand { left: 158px; top: 28px; }
  .envelope-back .brand-name { font-size: 10px; }
  .envelope-back .brand-name .dot { width: 6px; height: 6px; }

  /* Business cards */
  .card-front { left: 196px; top: 893px; width: 167px; height: 90px; }
  .card-front .brand { left: 62px; top: 14px; }
  .card-front .brand-name { font-size: 9px; }
  .card-front .brand-name .dot { width: 5px; height: 5px; }
  .card-front .brand-tag { font-size: 4.4px; }
  .card-front .person { position: absolute; right: 12px; top: 58px; text-align: right; }
  .card-front .person-name { font-size: 5.4px; font-weight: 700; letter-spacing: 0.04em; }
  .card-front .person-role { font-size: 4.2px; color: var(--muted); }
  .card-front .rule { position: absolute; left: 50px; right: 12px; top: 72px; border-top: 1px solid var(--rule); }
  .card-front .contact { position: absolute; right: 12px; top: 74px; text-align: right; font-size: 4px; line-height: 5.2px; color: #333; }
  .card-back { left: 406px; top: 893px; width: 136px; height: 90px; background: var(--folder); }
  .card-back .brand { left: 50px; top: 15px; color: var(--silver); }
  .card-back .brand-name { font-size: 9px; }
  .card-back .brand-name .dot { width: 5px; height: 5px; }
  .card-back .brand-tag { font-size: 4.4px; }

  /* Compliment slip */
  .compliment-slip { left: 616px; top: 883px; width: 401px; height: 190px; }
  .compliment-slip .brand { left: 24px; top: 30px; }
  .compliment-slip .brand-name { font-size: 14px; }
  .compliment-slip .brand-name .dot { width: 8px; height: 8px; }
  .compliment-slip .brand-tag { font-size: 6.2px; }
  .compliment-slip .script { position: absolute; right: 40px; top: 136px; font-family: "Great Vibes", cursive; font-size: 17px; }
  .compliment-slip .rule { position: absolute; left: 24px; right: 40px; top: 160px; border-top: 1px solid var(--rule); }
  .compliment-slip .contact { position: absolute; right: 40px; top: 165px; text-align: right; font-size: 5.4px; line-height: 7px; color: #333; }
</style>
</head>
<body>

  <section class="piece letterhead">
    <div class="brand">
      <div class="brand-name"><span class="dot"></span>Nordkante AG</div>
      <div class="brand-tag">DIGITALE STRATEGIEN</div>
    </div>
    <div class="letter-body">
      <p class="greeting">Dear sir,</p>
      <p>Thank you for your interest in our work. We plan, build and grow digital products for companies of every size. Our team combines search, content and software skills in one place, so every project moves quickly and clearly from idea to launch.</p>
      <p>This letter outlines the next steps of our cooperation. We will start with a short review of your current channels, then agree on goals, timing and budget. After that, we prepare a detailed plan and share regular reports so you always know where things stand.</p>
      <p>Please let us know if you have any questions. We look forward to working with you.</p>
    </div>
    <div class="closing">Yours Sincerely,<strong>Lena Hart</strong></div>
    <div class="signature" role="img" aria-label="Handwritten signature"></div>
    <div class="footer-rule"></div>
    <div class="letter-footer">
      Birkenweg 14, 20095 Hamburg, Germany · <strong>Tel:</strong> +49-(40)-5550-1234<br>
      <strong>Email:</strong> jonas@nordkante.de · <strong>Web:</strong> www.nordkante.de
    </div>
  </section>

  <section class="piece folder">
    <div class="spine"></div>
    <div class="brand">
      <div class="brand-name"><span class="dot"></span>Nordkante AG</div>
      <div class="brand-tag">DIGITALE STRATEGIEN</div>
    </div>
  </section>

  <section class="piece envelope-front">
    <div class="brand">
      <div class="brand-name"><span class="dot"></span>Nordkante AG</div>
      <div class="brand-tag">DIGITALE STRATEGIEN</div>
    </div>
    <div class="return">Birkenweg 14<br>20095 Hamburg, Germany</div>
  </section>

  <section class="piece envelope-back">
    <div class="brand">
      <div class="brand-name"><span class="dot"></span>Nordkante AG</div>
    </div>
    <div class="flap"></div>
  </section>

  <section class="piece card-front">
    <div class="brand">
      <div class="brand-name"><span class="dot"></span>Nordkante AG</div>
      <div class="brand-tag">DIGITALE STRATEGIEN</div>
    </div>
    <div class="person">
      <div class="person-name">JONAS BERGER</div>
      <div class="person-role">Managing Director</div>
    </div>
    <div class="rule"></div>
    <div class="contact">
      Birkenweg 14, 20095 Hamburg, Germany<br>
      +49-(40)-5550-1234 · jonas@nordkante.de
    </div>
  </section>

  <section class="piece card-back">
    <div class="brand">
      <div class="brand-name"><span class="dot"></span>Nordkante AG</div>
      <div class="brand-tag">DIGITALE STRATEGIEN</div>
    </div>
  </section>

  <section class="piece compliment-slip">
    <div class="brand">
      <div class="brand-name"><span class="dot"></span>Nordkante AG</div>
      <div class="brand-tag">DIGITALE STRATEGIEN</div>
    </div>
    <div class="script">With Compliments</div>
    <div class="rule"></div>
    <div class="contact">
      Birkenweg 14, 20095 Hamburg, Germany · <strong>Tel:</strong> +49-(40)-5550-1234<br>
      <strong>Email:</strong> jonas@nordkante.de · <strong>Web:</strong> www.nordkante.de
    </div>
  </section>

</body>
</html>
```